Osgood Business Card Design

Photography business needs a logo. I would like to see creative licence on options on 1 & 2 sided. I really like the concept of a fully / partially frosted design. I have already used ArtSwarm for my Logo, so I am looking for the same level of assistance with this project.

Industry/Entity Type

Business

Font styles to use
Serif
Script

Requirements
Must have
• Must Have:
• - These are my contact details
• Name: Pim L Osgood
• Mobile: 5813409271
• email: marlaweskin@fernpost.example

```html
<!DOCTYPE html>
<html lang="en">
<head>
<meta charset="utf-8">
<title>Osgood Business Card</title>
<link rel="stylesheet" href="https://fonts.googleapis.com/css2?family=Open+Sans:wght@400;700&display=swap">
<style>
  :root {
    --backdrop: #2a2a2c;
    --card-front: #ffffff;
    --card-back: #efefef;
    --brand-blue: #1aa9e8;
    --ink-dark: #2b2b2b;
  }
  * { box-sizing: border-box; margin: 0; padding: 0; }
  html, body {
    width: 1200px;
    height: 800px;
    overflow: hidden;
    background: var(--backdrop);
    font-family: "Open Sans", sans-serif;
  }
  .stage {
    position: relative;
    width: 1200px;
    height: 800px;
  }
  .card {
    position: absolute;
    width: 500px;
    height: 286px;
    top: 257px;
    box-shadow: 0 6px 18px rgba(0,0,0,0.45);
  }
  .card--front { left: 70px; background: var(--card-front); }
  .card--back  { left: 630px; background: var(--card-back); }

  .brand {
    display: flex;
    align-items: center;
    gap: 14px;
    color: var(--brand-blue);
    font-weight: 700;
  }
  .brand__dot {
    border-radius: 50%;
    background: var(--brand-blue);
  }
  .card--front .brand {
    position: absolute;
    inset: 0;
    justify-content: center;
    font-size: 64px;
  }
  .card--front .brand__dot { width: 54px; height: 54px; }

  .card--back .brand {
    position: absolute;
    top: 48px;
    right: 42px;
    font-size: 26px;
    gap: 8px;
  }
  .card--back .brand__dot { width: 24px; height: 24px; }

  .contact {
    position: absolute;
    left: 48px;
    bottom: 52px;
  }
  .contact__name {
    font-weight: 700;
    font-size: 17px;
    color: var(--ink-dark);
    line-height: 1.1;
  }
  .contact__role {
    font-size: 12px;
    color: var(--brand-blue);
    margin-bottom: 18px;
  }
  .contact__line {
    display: flex;
    align-items: center;
    gap: 14px;
    font-size: 12.5px;
    color: var(--brand-blue);
    margin-top: 8px;
  }
  .contact__icon {
    width: 14px;
    height: 14px;
    flex: none;
  }
</style>
</head>
<body>
<main class="stage">
  <section class="card card--front" aria-label="Card front">
    <div class="brand">
      <span class="brand__dot"></span>
      <span class="brand__name">Osgood</span>
    </div>
  </section>

  <section class="card card--back" aria-label="Card back">
    <div class="brand">
      <span class="brand__dot"></span>
      <span class="brand__name">Osgood</span>
    </div>

    <div class="contact">
      <p class="contact__name">Pim L Osgood</p>
      <p class="contact__role">Photo Manager</p>
      <p class="contact__line">
        <svg class="contact__icon" viewBox="0 0 14 14" aria-hidden="true">
          <rect x="3.5" y="0.5" width="7" height="13" rx="1.2" fill="none" stroke="#2b2b2b" stroke-width="1.2"/>
          <line x1="5.5" y1="11.3" x2="8.5" y2="11.3" stroke="#2b2b2b" stroke-width="1"/>
        </svg>
        <span>Mobile: 5813409271</span>
      </p>
      <p class="contact__line">
        <svg class="contact__icon" viewBox="0 0 14 14" aria-hidden="true">
          <rect x="0.5" y="2.5" width="13" height="9" fill="#2b2b2b"/>
          <polyline points="0.5,2.5 7,8 13.5,2.5" fill="none" stroke="#efefef" stroke-width="1"/>
        </svg>
        <span>Email: marlaweskin@fernpost.example</span>
      </p>
    </div>
  </section>
</main>
</body>
</html>
```